Varentoria Business Card and Letter Head

We are a leadership assessment consultancy based in Sydney, Australia. We help executive-level decison-makers select leaders for more senior level roles in corporate and government organisations. Our methodology is based on the latest research from the field of neuroscience.
We need a business card design and matching letter head that presents our company, Varentoria, as a:
1. trusted adviser to senior executive-level decison makers
2. niche consultancy who are experts in the field of assessing leadership talent
3. results-focused solution provider who balance scientific methods with pragmatic solutions
The following company details should be used in all designs:
Company Name: Varentoria
Details (for business card):
Derek Hanford
Prime Capacity Officer
Level 29, Marlow Tower
7 Marlow Square
Sydney, NSW 2000 Australia
Phone: 1300 582 714
Mobile: 0412 637 258
Email: derek.hanford@varentoria-example.com.au
Website: varentoria-example.com.au
I have attached the logo for Varentoria (for both a white and black background) - your business card and letter head designs must incoporate this logo and colour scheme.
Thanks for your interest in this project, I'm looking forward to receiving your ideas.
Regards,
Derek
Target Market(s)
Executive-level decison-makers in corporate and government organisations (e.g., CEO, VP, Head of Human Resources)
Industry/Entity Type
Leadership
Look and feel

```html
<!DOCTYPE html>
<html lang="en">
<head>
<meta charset="utf-8">
<title>Varentoria Business Cards</title>
<link rel="stylesheet" href="https://fonts.googleapis.com/css2?family=PT+Sans:wght@400;700&display=swap">
<style>
  :root {
    --stage: #ebe8e5;
    --paper: #ffffff;
    --ink: #3d3d3f;
    --rule: #4a4a4c;
    --brand-red: #c8371c;
    --band-light: #e7a58f;
    --band-mid: #d8694b;
    --band-dark: #c94a2c;
    --edge: #5a5a5a;
  }
  * { box-sizing: border-box; margin: 0; padding: 0; }
  html, body { width: 1200px; height: 741px; overflow: hidden; }
  body {
    background: var(--stage);
    font-family: "PT Sans", Arial, sans-serif;
    color: var(--ink);
    position: relative;
  }
  .card {
    position: absolute;
    width: 491px;
    height: 281px;
    border-radius: 15px;
    overflow: hidden;
    background: var(--paper);
    border: 1px solid var(--edge);
  }
  .card--front-lined { left: 100px; top: 63px; }
  .card--front-plain { left: 649px; top: 63px; }
  .card--back {
    left: 375px; top: 392px;
    border: none;
    background: radial-gradient(ellipse 62% 58% at 50% 44%, #ffffff 0%, #fbe6df 30%, #eb9c86 62%, #d4492b 85%, #c8371c 100%);
    box-shadow: 0 2px 4px rgba(0,0,0,0.15);
  }
  .brand {
    position: absolute;
    left: 0; right: 0;
    display: flex;
    align-items: center;
    justify-content: center;
    gap: 12px;
  }
  .card--front-lined .brand, .card--front-plain .brand { top: 44px; }
  .card--back .brand { top: 118px; }
  .brand__mark { width: 22px; height: 22px; background: var(--brand-red); }
  .brand__name { font-weight: 700; font-size: 46px; line-height: 1; color: var(--ink); letter-spacing: -0.5px; }
  .rule { position: absolute; left: 0; right: 0; height: 2px; background: var(--rule); }
  .band {
    position: absolute;
    left: 0; right: 0;
    top: 149px; height: 94px;
    background: linear-gradient(90deg, var(--band-light) 0%, var(--band-mid) 45%, var(--band-dark) 100%);
    color: #fff;
  }
  .holder { position: absolute; right: 300px; top: 29px; text-align: right; }
  .holder__name { font-weight: 700; font-size: 15px; letter-spacing: 0.3px; }
  .holder__role { font-size: 11px; margin-top: 2px; }
  .divider { position: absolute; left: 211px; top: 14px; width: 1px; height: 72px; background: #fff; opacity: 0.85; }
  .contacts { position: absolute; left: 225px; top: 17px; list-style: none; font-size: 11px; line-height: 15.5px; }
  .contacts li { display: flex; align-items: center; gap: 6px; }
  .contacts svg { width: 10px; height: 10px; flex: none; }
  .address { position: absolute; left: 0; right: 0; text-align: center; font-size: 13px; color: #333; }
  .card--front-lined .address { top: 257px; }
  .card--front-plain .address { top: 251px; }
</style>
</head>
<body>

<section class="card card--front-lined" aria-label="Card front with rules">
  <div class="brand"><span class="brand__mark"></span><span class="brand__name">Varentoria</span></div>
  <div class="rule" style="top:142px"></div>
  <div class="band">
    <div class="holder"><p class="holder__name">Derek Hanford</p><p class="holder__role">Prime Capacity Officer</p></div>
    <div class="divider"></div>
    <ul class="contacts">
      <li><svg viewBox="0 0 10 10"><circle cx="5" cy="5" r="4.5" fill="none" stroke="#fff"/><path d="M3 3.5 Q5 7 7 6.5" stroke="#fff" fill="none"/></svg>1300 582 714</li>
      <li><svg viewBox="0 0 10 10"><rect x="2.5" y="0.5" width="5" height="9" rx="1" fill="none" stroke="#fff"/><rect x="3.5" y="2" width="3" height="3" fill="#fff"/></svg>0412 637 258</li>
      <li><svg viewBox="0 0 10 10"><rect x="0.5" y="2" width="9" height="6" fill="#fff"/><path d="M0.5 2 L5 5.5 L9.5 2" stroke="#d8694b" fill="none"/></svg>derek.hanford@varentoria-example.com.au</li>
      <li><svg viewBox="0 0 10 10"><circle cx="5" cy="5" r="4.5" fill="#fff"/><path d="M0.5 5 H9.5 M5 0.5 V9.5" stroke="#d8694b" stroke-width="0.8"/></svg>www.varentoria-example.com.au</li>
    </ul>
  </div>
  <div class="rule" style="top:245px"></div>
  <p class="address">Level 29, Marlow Tower 7 Marlow Square Sydney, NSW 2000 Australia</p>
</section>

<section class="card card--front-plain" aria-label="Card front without rules">
  <div class="brand"><span class="brand__mark"></span><span class="brand__name">Varentoria</span></div>
  <div class="band">
    <div class="holder"><p class="holder__name">Derek Hanford</p><p class="holder__role">Prime Capacity Officer</p></div>
    <div class="divider"></div>
    <ul class="contacts">
      <li><svg viewBox="0 0 10 10"><circle cx="5" cy="5" r="4.5" fill="none" stroke="#fff"/><path d="M3 3.5 Q5 7 7 6.5" stroke="#fff" fill="none"/></svg>1300 582 714</li>
      <li><svg viewBox="0 0 10 10"><rect x="2.5" y="0.5" width="5" height="9" rx="1" fill="none" stroke="#fff"/><rect x="3.5" y="2" width="3" height="3" fill="#fff"/></svg>0412 637 258</li>
      <li><svg viewBox="0 0 10 10"><rect x="0.5" y="2" width="9" height="6" fill="#fff"/><path d="M0.5 2 L5 5.5 L9.5 2" stroke="#d8694b" fill="none"/></svg>derek.hanford@varentoria-example.com.au</li>
      <li><svg viewBox="0 0 10 10"><circle cx="5" cy="5" r="4.5" fill="#fff"/><path d="M0.5 5 H9.5 M5 0.5 V9.5" stroke="#d8694b" stroke-width="0.8"/></svg>www.varentoria-example.com.au</li>
    </ul>
  </div>
  <p class="address">Level 29, Marlow Tower 7 Marlow Square Sydney, NSW 2000 Australia</p>
</section>

<section class="card card--back" aria-label="Card back">
  <div class="brand"><span class="brand__mark"></span><span class="brand__name">Varentoria</span></div>
</section>

</body>
</html>
```